Sparrow Haulage needs a business card design.

Design a double-sided business card for new freight business. On the front, would like to see our logo along with the following info:

Martin Obuya
CEO/FOUNDER
555-206-7142
martinobuya@sparrow-haulage.example

On the reverse side, we would like to use the graphic image of our logo only without the Sparrow Haulage name.

```html
<!DOCTYPE html>
<html lang="en">
<head>
<meta charset="UTF-8">
<title>Sparrow Haulage – Business Card</title>
<link href="https://fonts.googleapis.com/css2?family=Arimo:wght@400;700&display=swap" rel="stylesheet">
<style>
  :root {
    --backdrop: #0d0d0d;
    --card: #1b1b1b;
    --accent-red: #b5070c;
    --mark-black: #080808;
    --text-white: #f2f2f2;
  }
  * { margin: 0; padding: 0; box-sizing: border-box; }
  html, body {
    width: 1200px; height: 900px; overflow: hidden;
    background: var(--backdrop);
    font-family: "Arimo", Arial, sans-serif;
  }
  .canvas {
    width: 1200px; height: 900px;
    display: flex; flex-direction: column;
    align-items: center; justify-content: center; gap: 44px;
  }
  .card {
    position: relative;
    width: 630px; height: 360px;
    background: var(--card);
    overflow: hidden;
  }
  .card::after {
    content: ""; position: absolute; left: 0; right: 0; bottom: 0;
    height: 9px; background: var(--accent-red);
  }

  /* Reverse side: symbol placeholder only, no company name */
  .card--back {
    display: flex; align-items: center; justify-content: center;
  }
  .back-symbol {
    width: 130px; height: 130px;
    background: var(--mark-black);
    margin-bottom: 20px;
  }

  /* Front side */
  .card--front { padding: 46px 0 0 54px; }
  .brand {
    display: flex; align-items: center; gap: 12px;
    color: var(--accent-red);
    font-weight: 700; font-size: 30px; letter-spacing: 3px;
    text-transform: uppercase; white-space: nowrap;
  }
  .brand__square { width: 26px; height: 26px; background: var(--accent-red); flex: none; }
  .person { margin: 58px 0 0 120px; }
  .person__name {
    color: var(--accent-red); font-weight: 700; font-size: 24px;
    text-transform: uppercase; letter-spacing: 0.5px;
  }
  .person__title {
    color: var(--text-white); font-size: 17px; margin-top: 2px;
  }
  .contacts { list-style: none; margin: 26px 0 0 100px; }
  .contacts li {
    display: flex; align-items: center; gap: 10px;
    color: var(--text-white); font-size: 16px; line-height: 26px;
    white-space: nowrap;
  }
  .contacts svg { width: 16px; height: 16px; flex: none; }
</style>
</head>
<body>
<main class="canvas">

  <section class="card card--back" aria-label="Card reverse">
    <div class="back-symbol" role="img" aria-label="Company symbol"></div>
  </section>

  <section class="card card--front" aria-label="Card front">
    <div class="brand">
      <span class="brand__square"></span>
      <span>Sparrow Haulage</span>
    </div>

    <div class="person">
      <p class="person__name">Martin Obuya</p>
      <p class="person__title">CEO/FOUNDER</p>
    </div>

    <ul class="contacts">
      <li>
        <svg viewBox="0 0 24 24" aria-hidden="true"><path fill="#b5070c" d="M6.6 10.8a15.1 15.1 0 0 0 6.6 6.6l2.2-2.2a1 1 0 0 1 1-.25 11.4 11.4 0 0 0 3.6.57 1 1 0 0 1 1 1V20a1 1 0 0 1-1 1A17 17 0 0 1 3 4a1 1 0 0 1 1-1h3.5a1 1 0 0 1 1 1c0 1.25.2 2.450.57 3.57a1 1 0 0 1-.25 1z"/></svg>
        555-206-7142
      </li>
      <li>
        <svg viewBox="0 0 24 24" aria-hidden="true"><rect x="2" y="5" width="20" height="14" fill="#b5070c"/><path d="M2 5l10 8 10-8" fill="none" stroke="#1b1b1b" stroke-width="1.8"/></svg>
        martinobuya@sparrow-haulage.example
      </li>
      <li>
        <svg viewBox="0 0 24 24" aria-hidden="true"><g fill="none" stroke="#b5070c" stroke-width="2"><circle cx="12" cy="12" r="9.5"/><ellipse cx="12" cy="12" rx="4" ry="9.5"/><path d="M2.5 12h19M4 7h16M4 17h16"/></g></svg>
        www.sparrow-haulage.example
      </li>
    </ul>
  </section>

</main>
</body>
</html>
```